Local fast-growing company in the service sector

We are looking for a modern business card design, which should also appear on our letterheads

Target Market(s)

Private and industrial sectors

Contact Information for Business Card

Vorname Name
Kellberger Str. 18
71409 Reuttal
Tel.: 07146-839214-0
Name@agentur-kvtl.de

Colors
9d9d9d
919191
aaaaaa

Requirements
Must have
• The logo (file) in silver

```html
<!DOCTYPE html>
<html lang="de">
<head>
<meta charset="utf-8">
<title>KVTL Visitenkarte</title>
<link href="https://fonts.googleapis.com/css2?family=Open+Sans:wght@400;600;700&display=swap" rel="stylesheet">
<style>
  :root {
    --backdrop: #3b3430;
    --card: #161616;
    --card-edge: #1f1f1f;
    --silver: #aaaaaa;
    --silver-mid: #9d9d9d;
    --silver-dark: #919191;
    --text-light: #e6e6e6;
  }
  * { margin: 0; padding: 0; box-sizing: border-box; }
  html, body { width: 1200px; height: 864px; overflow: hidden; }
  body {
    background: var(--backdrop);
    font-family: "Open Sans", Arial, sans-serif;
    position: relative;
  }
  .card {
    position: absolute;
    width: 540px;
    height: 327px;
    background: var(--card);
    border: 1px solid var(--card-edge);
    box-shadow: 0 18px 40px rgba(0,0,0,0.45);
  }
  .card--front { left: 50px; top: 80px; }
  .card--back { left: 610px; top: 440px; }

  .brand {
    display: flex;
    align-items: center;
    gap: 14px;
    position: absolute;
  }
  .brand__square {
    width: 40px; height: 40px;
    background: var(--silver-dark);
  }
  .brand__name {
    font-weight: 700;
    font-size: 56px;
    line-height: 1;
    letter-spacing: 2px;
    color: var(--silver);
  }
  .card--front .brand { left: 120px; top: 95px; }
  .front__web {
    position: absolute;
    left: 0; right: 0;
    top: 212px;
    text-align: center;
    font-size: 15px;
    letter-spacing: 6px;
    color: var(--silver-dark);
  }

  .card--back .brand { left: 220px; top: 72px; }
  .brand--small .brand__name { font-size: 50px; }
  .brand--small .brand__square { width: 36px; height: 36px; }

  .contact {
    position: absolute;
    left: 30px; right: 30px;
    top: 200px;
    display: flex;
    align-items: stretch;
    color: var(--text-light);
    font-size: 16px;
    line-height: 1.35;
  }
  .contact__person {
    text-align: right;
    padding-right: 18px;
    width: 200px;
  }
  .contact__name {
    font-weight: 700;
    color: var(--silver-mid);
    letter-spacing: 0.5px;
  }
  .contact__divider {
    width: 1px;
    background: var(--silver-dark);
  }
  .contact__lines {
    list-style: none;
    padding-left: 18px;
    padding-top: 10px;
  }
  .contact__lines li {
    display: flex;
    align-items: center;
    gap: 8px;
  }
  .contact__icon { width: 12px; height: 12px; fill: var(--silver); flex: none; }
</style>
</head>
<body>

<section class="card card--front" aria-label="Vorderseite">
  <div class="brand">
    <span class="brand__square"></span>
    <span class="brand__name">KVTL</span>
  </div>
  <p class="front__web">www.agentur-kvtl.de</p>
</section>

<section class="card card--back" aria-label="Rückseite">
  <div class="brand brand--small">
    <span class="brand__square"></span>
    <span class="brand__name">KVTL</span>
  </div>
  <div class="contact">
    <div class="contact__person">
      <p class="contact__name">JONAS KELLER</p>
      <p>Kellberger Str. 18</p>
      <p>71409 Reuttal</p>
    </div>
    <span class="contact__divider"></span>
    <ul class="contact__lines">
      <li>
        <svg class="contact__icon" viewBox="0 0 12 12" aria-hidden="true"><path d="M2 1h2l1 3-1.5 1a6 6 0 0 0 3.5 3.5L8 7l3 1v2a1 1 0 0 1-1 1A9 9 0 0 1 1 2a1 1 0 0 1 1-1z"/></svg>
        <span>07146-839214-0</span>
      </li>
      <li>
        <svg class="contact__icon" viewBox="0 0 12 12" aria-hidden="true"><path d="M1 3h10v7H1z M1 3l5 4 5-4" fill="none" stroke="#aaaaaa" stroke-width="1.3"/></svg>
        <span>Name@agentur-kvtl.de</span>
      </li>
      <li>
        <svg class="contact__icon" viewBox="0 0 12 12" aria-hidden="true"><circle cx="6" cy="6" r="5" fill="none" stroke="#aaaaaa" stroke-width="1.2"/><path d="M1 6h10M6 1c-2 3-2 7 0 10M6 1c2 3 2 7 0 10" fill="none" stroke="#aaaaaa" stroke-width="1"/></svg>
        <span>www.agentur-kvtl.de</span>
      </li>
    </ul>
  </div>
</section>

</body>
</html>
```